IT Company looking to market towards Dental Offices

I am looking for a full-color design. Using my existing logo. Must have High Res stock photos. The brochure needs to be full page edge to edge design single fold pamphlet style. Content provided. Please see the website in attached Word Doc for more content.

```html
<!DOCTYPE html>
<html lang="en">
<head>
<meta charset="UTF-8">
<title>Byte Medics – Dental Practice Brochure</title>
<link href="https://fonts.googleapis.com/css2?family=Open+Sans:wght@300;400;600;700;800&display=swap" rel="stylesheet">
<style>
  :root {
    --stage: #4a4a4a;
    --paper: #f4f5f7;
    --navy: #0f1d5c;
    --blue: #1a6fc4;
    --band-blue: #2479c9;
    --ink: #4a4f58;
    --white: #ffffff;
    --stone-light: #b9b6b1;
    --stone-mid: #a3a09b;
    --stone-dark: #85827d;
    --photo-light: #e6f1fb;
    --photo-mid: #a9cdee;
  }
  * { margin: 0; padding: 0; box-sizing: border-box; }
  html, body {
    width: 1200px; height: 824px; overflow: hidden;
    background: var(--stage);
    font-family: "Open Sans", sans-serif;
  }
  .spread {
    position: absolute; left: 49px; top: 22px;
    width: 1102px; height: 780px;
    display: flex;
  }
  .page {
    position: relative; width: 551px; height: 780px;
    background: var(--paper); overflow: hidden;
  }

  /* Back cover */
  .back-photo {
    position: absolute; left: 0; top: 0; width: 100%; height: 470px;
    background: linear-gradient(135deg, var(--stone-light) 0%, var(--stone-mid) 50%, var(--stone-dark) 100%);
  }
  .back-band {
    position: absolute; left: 0; top: 470px; width: 100%; height: 150px;
    background: var(--band-blue); color: var(--white);
    padding: 26px 40px 0 40px;
    font-size: 12.5px; line-height: 1.55; font-weight: 400;
  }
  .back-cta {
    position: absolute; left: 40px; top: 650px; right: 40px;
    color: var(--ink); font-size: 13px; line-height: 1.5; font-weight: 300;
  }
  .back-cta .url { color: var(--navy); font-weight: 700; }

  /* Front cover */
  .front-art { position: absolute; inset: 0; }
  .brand {
    position: absolute; left: 140px; top: 62px;
    display: flex; align-items: center; gap: 12px;
  }
  .brand-dot {
    width: 44px; height: 44px; border-radius: 50%; background: var(--navy);
  }
  .brand-name {
    font-size: 30px; font-weight: 700; color: var(--navy); letter-spacing: 0.3px;
  }
  .badge-text {
    position: absolute; left: 345px; top: 425px; width: 170px;
    text-align: center; color: var(--white); line-height: 1.1;
  }
  .badge-text .light { font-size: 12px; font-weight: 300; display: block; }
  .badge-text .strong-lg { font-size: 25px; font-weight: 800; display: block; letter-spacing: 0.5px; }
  .badge-text .strong { font-size: 17px; font-weight: 800; display: block; }
  .front-web {
    position: absolute; right: 40px; top: 680px;
    display: flex; align-items: center; gap: 7px;
    font-size: 13px; color: var(--navy);
  }
  .front-web b { font-weight: 700; }
</style>
</head>
<body>
<main class="spread">

  <section class="page back-cover">
    <div class="back-photo" role="img" aria-label="Photo of a steel bank vault door set into rough stone"></div>
    <div class="back-band">
      <p>Byte Medics offers proven expertise in Dental Practices. We have trained engineers that specialize in Dental practices. We can handle supporting you Practice Management Software to installing IOCs, Remote &amp; Sensors, Pano's, X-rays, scanners, and pen pads. Being familiar with the Digital side of how your practice runs we will be able to predict and plan for your growth by providing the correct configurations and storage needs you will require. We know Dental!</p>
    </div>
    <div class="back-cta">
      <p>Get started today at <span class="url">www.toothsafevault.com</span><br>
      We don't charge anything until we have confirmation that your Data has been successfully backed up on our encrypted servers.</p>
    </div>
  </section>

  <section class="page front-cover">
    <svg class="front-art" width="551" height="780" viewBox="0 0 551 780">
      <defs>
        <clipPath id="photo-clip"><circle cx="350" cy="400" r="225"/></clipPath>
        <linearGradient id="photo-fill" x1="0" y1="0" x2="1" y2="1">
          <stop offset="0" stop-color="var(--photo-mid)"/>
          <stop offset="0.55" stop-color="var(--photo-light)"/>
          <stop offset="1" stop-color="var(--photo-mid)"/>
        </linearGradient>
      </defs>
      <path d="M470 0 Q520 10 551 40 L551 0 Z" fill="var(--blue)"/>
      <path d="M168 340 A245 245 0 0 1 551 200 L551 184 A260 260 0 0 0 154 336 Z" fill="var(--navy)"/>
      <path d="M116 430 A238 238 0 0 0 470 612 L480 625 A252 252 0 0 1 102 432 Z" fill="var(--navy)"/>
      <g role="img" aria-label="Photo of a bright modern dental treatment room with patient chair">
        <rect x="100" y="150" width="451" height="500" fill="url(#photo-fill)" clip-path="url(#photo-clip)"/>
      </g>
      <circle cx="430" cy="470" r="96" fill="none" stroke="var(--navy)" stroke-width="1"/>
      <circle cx="430" cy="470" r="88" fill="var(--blue)"/>
    </svg>

    <div class="brand">
      <span class="brand-dot"></span>
      <span class="brand-name">Byte Medics</span>
    </div>

    <div class="badge-text">
      <span class="light">Byte Medics</span>
      <span class="strong-lg">OFFERS</span>
      <span class="light">proven expertise in</span>
      <span class="strong">DENTAL<br>PRACTICES</span>
    </div>

    <div class="front-web">
      <svg width="12" height="12" viewBox="0 0 12 12" aria-hidden="true">
        <circle cx="6" cy="6" r="5.3" fill="none" stroke="var(--blue)" stroke-width="1.2"/>
        <ellipse cx="6" cy="6" rx="2.3" ry="5.3" fill="none" stroke="var(--blue)" stroke-width="1"/>
        <line x1="0.7" y1="6" x2="11.3" y2="6" stroke="var(--blue)" stroke-width="1"/>
      </svg>
      <span>www.<b>riverdalebytes</b>.com</span>
    </div>
  </section>

</main>
</body>
</html>
```